Lanternfield Drinks business cards

We need a business card design for our new logo. The company is modern, progressive, professional, yet approachable. The key products are ready to drink bottles and cans of coffee based beverages.
These cards will be a critical part of the first impression made by our sales organization, business development team, and all external facing personnel.
Card can be a vertical or horizontal orientation.

Target Market(s)

Customers, suppliers, business partners

Industry/Entity Type

Business

Contact Information for Business Card

Business cards should feature Company Name and Logo.

Font styles to use
Serif

Colors

Designer to choose colors to be used in the design.

Requirements
Must have
• Strong readability of Name, phone #, mobile number and email address.
• Job title, website url, Street Address, and other details can be secondary level readability.
Nice to have
• High impact, simplistic quality design.
• Ok to utilize the 'H in the box' separate from the company name

```html
<!DOCTYPE html>
<html lang="en">
<head>
<meta charset="utf-8">
<title>Lanternfield Drinks Business Cards</title>
<link href="https://fonts.googleapis.com/css2?family=Lato:wght@400;700&display=swap" rel="stylesheet">
<style>
  :root {
    --backdrop: #555555;
    --paper: #ffffff;
    --ink: #222222;
    --night: #000000;
    --brand-orange: #f05a28;
    --brand-amber: #f7941d;
    --rule: #cfcfcf;
  }
  html, body {
    margin: 0;
    padding: 0;
    width: 1200px;
    height: 900px;
    overflow: hidden;
    background: var(--backdrop);
    font-family: 'Lato', sans-serif;
  }
  .canvas { position: relative; width: 1200px; height: 900px; }
  .card {
    position: absolute;
    top: 306px;
    width: 439px;
    height: 271px;
    box-shadow: 2px 3px 5px rgba(0,0,0,0.45);
  }
  .card--front { left: 149px; background: var(--paper); }
  .card--back { left: 608px; width: 441px; height: 272px; background: var(--night); }

  .brand-square {
    position: absolute;
    box-sizing: border-box;
    border: 3px solid var(--brand-orange);
  }
  .brand-name {
    position: absolute;
    margin: 0;
    font-weight: 700;
    color: var(--brand-orange);
    white-space: nowrap;
    letter-spacing: 0.02em;
  }
  .card--front .brand-square { left: 31px; top: 18px; width: 42px; height: 42px; border-width: 2px; }
  .card--front .brand-name { left: 80px; top: 30px; font-size: 13.5px; }
  .card--back .brand-square { left: 47px; top: 98px; width: 75px; height: 75px; }
  .card--back .brand-name { left: 134px; top: 120px; font-size: 23.5px; }

  .person {
    position: absolute;
    right: 29px;
    top: 30px;
    text-align: right;
  }
  .person__name { margin: 0; font-size: 17px; font-weight: 400; color: var(--brand-orange); line-height: 20px; }
  .person__role { margin: 0; font-size: 12.5px; color: var(--brand-amber); line-height: 14px; }

  .divider {
    position: absolute;
    left: 31px;
    top: 176px;
    width: 378px;
    height: 1px;
    background: var(--rule);
  }
  .contacts {
    position: absolute;
    left: 31px;
    top: 184px;
    margin: 0;
    padding: 0;
    list-style: none;
    font-size: 13px;
    color: var(--ink);
  }
  .contacts li { display: flex; align-items: center; height: 16.7px; }
  .contacts svg { width: 13px; height: 13px; margin-right: 6px; flex: none; }
  .address {
    position: absolute;
    right: 29px;
    top: 202px;
    display: flex;
    align-items: flex-start;
    font-size: 13px;
    color: var(--ink);
  }
  .address p { margin: 0; text-align: right; line-height: 16px; }
  .address svg { width: 13px; height: 13px; margin-left: 5px; margin-top: 2px; }
</style>
</head>
<body>
<div class="canvas">

  <section class="card card--front">
    <span class="brand-square"></span>
    <p class="brand-name">LANTERNFIELD DRINKS</p>

    <div class="person">
      <p class="person__name">LORUM SMITH</p>
      <p class="person__role">Managing Director</p>
    </div>

    <div class="divider"></div>

    <ul class="contacts">
      <li>
        <svg viewBox="0 0 13 13"><rect width="13" height="13" rx="2.5" fill="var(--brand-orange)"/><path d="M4 3.2l1.3 0 .6 1.8-.9.6c.4.9 1 1.5 1.9 1.9l.6-.9 1.8.6v1.3c0 .4-.3.7-.8.7C6 9.1 3.9 7 3.3 4 3.3 3.5 3.6 3.2 4 3.2z" fill="#fff"/></svg>
        888 555 4433
      </li>
      <li>
        <svg viewBox="0 0 13 13"><rect width="13" height="13" rx="2.5" fill="var(--brand-orange)"/><rect x="4.3" y="2.6" width="4.4" height="7.8" rx="0.8" fill="none" stroke="#fff" stroke-width="1.1"/></svg>
        888 444 0000
      </li>
      <li>
        <svg viewBox="0 0 13 13"><rect width="13" height="13" rx="2.5" fill="var(--brand-orange)"/><rect x="3" y="4" width="7" height="5" fill="#fff"/><path d="M3 4l3.5 2.6L10 4" fill="none" stroke="var(--brand-orange)" stroke-width="0.9"/></svg>
        info@webname.com
      </li>
      <li>
        <svg viewBox="0 0 13 13"><rect width="13" height="13" rx="2.5" fill="var(--brand-orange)"/><circle cx="6.5" cy="6.5" r="3.4" fill="#fff"/><circle cx="6.5" cy="6.5" r="1.4" fill="var(--brand-orange)"/></svg>
        www.webname.com
      </li>
    </ul>

    <div class="address">
      <p>421, Address line here,<br>Dummy Code, 45452<br>Country Name</p>
      <svg viewBox="0 0 13 13"><rect width="13" height="13" rx="2.5" fill="var(--brand-orange)"/><path d="M6.5 2.5a2.6 2.6 0 0 1 2.6 2.6c0 2-2.6 4.6-2.6 4.6S3.9 7.1 3.9 5.1A2.6 2.6 0 0 1 6.5 2.5z" fill="#fff"/><circle cx="6.5" cy="5.1" r="1" fill="var(--brand-orange)"/></svg>
    </div>
  </section>

  <section class="card card--back">
    <span class="brand-square"></span>
    <p class="brand-name">LANTERNFIELD DRINKS</p>
  </section>

</div>
</body>
</html>
```